Kestrada LLC, needs a web page no more than 5 pages (for now)

Kestrada is a general contractor. Our services include general contracting, design-build construction, disaster recovery and environmental remediation. Our main clients are PMX, TQ, State and Local Gov't Agencies, Hospitals and Schools. Kestrada is also a SDVOSB.

```html
<!DOCTYPE html>
<html lang="en">
<head>
<meta charset="utf-8">
<title>Kestrada LLC — General Contractor</title>
<link href="https://fonts.googleapis.com/css2?family=Jost:wght@300;400;500;600&display=swap" rel="stylesheet">
<style>
:root{
  --canvas:#ffffff;
  --page:#1c1c1c;
  --band:#2a2a2a;
  --card:#262626;
  --text:#f2f2f2;
  --muted:#a9a9a9;
  --gold:#c9a93a;
  --line:#353535;
}
*{box-sizing:border-box;margin:0;padding:0}
html,body{width:1200px;height:1200px;overflow:hidden;background:var(--canvas)}
body{font-family:'Jost',sans-serif;color:var(--text);position:relative}
.page{position:absolute;left:433px;top:0;width:538px;height:1932px;background:var(--page);transform:scale(0.62112);transform-origin:0 0;overflow:hidden}
.abs{position:absolute}
.photo{position:absolute;border-radius:6px;overflow:hidden}
.hero{left:0;top:0;width:538px;height:308px;border-radius:0;background:radial-gradient(ellipse at 55% 70%,#c98a4e 0%,rgba(140,90,60,.6) 20%,transparent 45%),linear-gradient(180deg,#3d4a66 0%,#4d5a74 35%,#2b2f3c 75%,#17181d 100%)}
.brand{left:55px;top:16px;display:flex;align-items:center;gap:5px;font-size:10px;font-weight:500;letter-spacing:1px;color:var(--gold)}
.brand i{width:9px;height:9px;border-radius:50%;background:var(--gold);display:block}
.nav{left:160px;top:18px;width:233px;height:20px;background:#fff;border-radius:10px;display:flex;justify-content:space-around;align-items:center;padding:0 10px}
.nav a{font-size:6px;font-weight:500;color:#222;text-decoration:none}
.lang{left:498px;top:25px;font-size:7px;font-weight:500}
.hero-title{left:41px;top:212px;font-size:24px;font-weight:300;line-height:24px}
.since{left:41px;top:268px;font-size:10px;font-weight:300}
.thumb{left:375px;top:196px;width:130px;height:72px;background:linear-gradient(135deg,#6b7a80,#c9c6a0 60%,#f2e8b8)}
.arrow{display:inline-block;width:16px;height:1px;background:currentColor;position:relative;vertical-align:middle;margin-left:5px}
.arrow:after{content:"";position:absolute;right:0;top:-2px;border:2.5px solid transparent;border-left:4px solid currentColor;border-right:0}
.arrow.gold{color:var(--gold)}
.proj-link{left:375px;top:274px;font-size:8px;font-weight:300}
.clients{left:0;top:308px;width:538px;height:47px;background:var(--band)}
.clients-label{left:41px;top:10px;font-size:11px;font-weight:300;line-height:15px}
.client{top:17px;font-size:10px;font-weight:500;color:#ddd;display:flex;align-items:center;gap:4px}
.client i{width:6px;height:6px;background:#ddd;display:block}
.eyebrow{font-size:9px;font-weight:300;color:var(--gold);letter-spacing:.3px}
.center{left:0;width:538px;text-align:center}
.h-mid{font-size:22px;font-weight:300;line-height:22px}
.small{font-size:5.6px;font-weight:300;line-height:10px;color:#d8d8d8}
.btn{border:1px solid var(--gold);border-radius:8px;font-size:6px;color:var(--gold);text-align:center;line-height:13px;width:62px;height:15px}
.svc{top:564px;width:152px;height:107px}
.svc-label{top:680px;font-size:8px;font-weight:300}
.rule{left:22px;top:722px;width:480px;height:1px;background:var(--line)}
.stat{top:728px}
.stat b{display:block;font-size:22px;font-weight:600;line-height:24px}
.stat span{display:block;font-size:7px;font-weight:300;line-height:7px}
.h-lg{font-size:21px;font-weight:300;line-height:22px}
.h-lg strong{font-weight:400}
.tcard{top:884px;width:175px;height:88px;background:var(--card);border-radius:6px;padding:12px 19px}
.tcard.fade{opacity:.3}
.stars{color:var(--gold);font-size:8px;letter-spacing:1px;line-height:10px}
.tcard p{font-size:5.2px;font-weight:300;line-height:9.5px;color:#d0d0d0;margin-top:4px}
.tcard .who{font-size:5.5px;margin-top:6px;color:#fff}
.tcard .who b{font-weight:600}
.tcard .who span{color:#999}
.quote{right:14px;top:10px;font-size:28px;color:#444;line-height:28px}
.nav-arrow{top:994px;width:22px;height:1px;background:#ddd}
.big{left:13px;top:1023px;width:512px;height:219px;background:linear-gradient(180deg,#3f7fc4 0%,#8cbbe6 55%,#c7cfc6 75%,#4f6d3d 100%)}
.crew{left:88px;top:1200px;width:176px;height:220px;border-radius:4px;background:radial-gradient(circle at 45% 25%,#d9a43a 0%,#8a6a3a 30%,#2f3a3e 75%)}
.col-title{font-size:10px;font-weight:400;line-height:11px}
.col-text{font-size:5.2px;font-weight:300;line-height:9px;color:#cfcfcf}
.cta{left:0;top:1657px;width:186px;height:100px;background:var(--band)}
.foot-link{font-size:9px;font-weight:300;line-height:18.5px}
.legal{top:1906px;font-size:5.5px;font-weight:300;color:#bbb}
</style>
</head>
<body>
<main class="page">

  <section class="photo hero" role="img" aria-label="Modern curved glass office building at dusk"></section>
  <div class="abs brand"><i></i>KESTRADA</div>
  <nav class="abs nav"><a>HOME</a><a>ABOUT</a><a>SERVICES</a><a>PROJECTS</a><a>CONTACT</a></nav>
  <div class="abs lang">De</div>
  <h1 class="abs hero-title">Led by<br>Excellence</h1>
  <div class="abs since">Since 1987</div>
  <div class="photo thumb" role="img" aria-label="Glass building project in sunlight"></div>
  <div class="abs proj-link">Our Projects <span class="arrow"></span></div>

  <section class="abs clients">
    <div class="abs clients-label">A few of our<br>exceptional clients</div>
    <div class="abs client" style="left:170px">Arbelo</div>
    <div class="abs client" style="left:248px">Lumora</div>
    <div class="abs client" style="left:333px"><i></i>Vantix</div>
    <div class="abs client" style="left:415px">Oxley</div>
    <div class="abs client" style="left:478px">Pendra</div>
  </section>

  <div class="abs center eyebrow" style="top:381px">WELCOME</div>
  <h2 class="abs center h-mid" style="top:398px">Get More With<br>Kestrada</h2>
  <p class="abs small" style="left:160px;top:450px;width:218px;text-align:center">We deliver general contracting, design-build and recovery work for public agencies, hospitals and schools. Our crews plan with care, build with precision and hand over on time. Veteran owned, safety driven, quality first.</p>
  <div class="abs btn" style="left:238px;top:505px">Our Services</div>

  <div class="photo svc" style="left:16px;background:linear-gradient(180deg,#6f8a6a,#b9a68a 55%,#dfe3e6)" role="img" aria-label="Modern house with pool over architectural plans"></div>
  <div class="photo svc" style="left:178px;background:linear-gradient(180deg,#c8c4bc,#8a857a 55%,#5e6a78)" role="img" aria-label="Worker in protective suit testing soil"></div>
  <div class="photo svc" style="left:340px;background:linear-gradient(160deg,#5aa7d8,#8a6a4a 40%,#4a3a30)" role="img" aria-label="Excavator clearing a damaged building"></div>
  <div class="photo svc" style="left:502px;background:linear-gradient(180deg,#1c2f58,#2d4a80)" role="img" aria-label="City buildings at night"></div>
  <div class="abs svc-label" style="left:16px">Design-Build Construction <span class="arrow gold"></span></div>
  <div class="abs svc-label" style="left:178px">Environmental Remediation <span class="arrow gold"></span></div>
  <div class="abs svc-label" style="left:340px">Disaster Recovery <span class="arrow gold"></span></div>
  <div class="abs svc-label" style="left:503px">General contracting</div>

  <div class="abs rule"></div>
  <div class="abs stat" style="left:108px"><b>75+</b><span>Project Completed</span></div>
  <div class="abs stat" style="left:234px"><b>30+</b><span>Trusted Customers</span></div>
  <div class="abs stat" style="left:359px"><b>3000+</b><span>Employees</span></div>

  <div class="abs eyebrow" style="left:24px;top:809px">TESTIMONIALS</div>
  <h2 class="abs h-lg" style="left:24px;top:827px">Over <strong>35 Years</strong><br>of Trust</h2>

  <article class="abs tcard" style="left:24px">
    <div class="abs quote">”</div>
    <div class="stars">★★★★★</div>
    <p>The team finished our clinic wing early and kept the site clean every single day. Clear updates, honest costs and solid work we can rely on.</p>
    <div class="who"><b>Mara Ellison</b> <span>· City of London</span></div>
  </article>
  <article class="abs tcard" style="left:215px">
    <div class="stars">★★★★★</div>
    <p>After the flood they had crews on site within hours. Every step was planned, priced and explained. We would hire them again for any job.</p>
    <div class="who"><b>Mara Ellison</b> <span>· City of London</span></div>
  </article>
  <article class="abs tcard fade" style="left:404px">
    <div class="stars">★★★★★</div>
    <p>Our school build ran on schedule with no safety issues. The site leads were calm, skilled and always ready to answer our questions fast.</p>
    <div class="who"><b>Mara Ellison</b> <span>· City of London</span></div>
  </article>
  <div class="abs nav-arrow" style="left:440px"></div>
  <div class="abs nav-arrow" style="left:472px"></div>

  <div class="photo big" role="img" aria-label="High-rise towers under construction with tower cranes"></div>
  <div class="photo crew" role="img" aria-label="Construction team in hard hats reviewing plans"></div>
  <h2 class="abs h-lg" style="left:284px;top:1267px">The leader in<br>Modern Construction</h2>
  <p class="abs col-text" style="left:284px;top:1320px;width:208px">From first sketch to final walkthrough we manage every trade, permit and deadline. Our project leads bring decades of field experience, modern tools and a steady focus on safety. We build hospitals, schools and public facilities that serve their communities for generations, and we stand behind every structure we hand over.</p>
  <div class="abs btn" style="left:284px;top:1393px">Our Services</div>

  <div class="abs eyebrow" style="left:24px;top:1452px">OUR COMMITMENT</div>
  <h2 class="abs" style="left:24px;top:1469px;font-size:14px;font-weight:300;line-height:17px">Committed To Quality Craftsmanship<br>Integrity And Lasting Client Satisfaction</h2>

  <svg class="abs" style="left:24px;top:1541px" width="13" height="13" viewBox="0 0 13 13" fill="#c9a93a"><rect x="0" y="0" width="4" height="4"/><rect x="9" y="0" width="4" height="4"/><rect x="4.5" y="4.5" width="4" height="4"/><rect x="0" y="9" width="4" height="4"/><rect x="9" y="9" width="4" height="4"/></svg>
  <svg class="abs" style="left:156px;top:1541px" width="13" height="13" viewBox="0 0 13 13" stroke="#c9a93a" stroke-width="1.3"><path d="M0 13L13 0M0 8L8 0M5 13L13 5M0 3L3 0M10 13L13 10"/></svg>
  <svg class="abs" style="left:288px;top:1541px" width="13" height="13" viewBox="0 0 13 13" fill="#c9a93a"><rect x="4.5" y="0" width="4" height="4"/><rect x="0" y="4.5" width="4" height="4"/><rect x="9" y="4.5" width="4" height="4"/><rect x="4.5" y="9" width="4" height="4"/></svg>
  <svg class="abs" style="left:421px;top:1541px" width="13" height="13" viewBox="0 0 13 13" fill="#c9a93a"><path d="M0 0L5 6.5L0 13ZM13 0L8 6.5L13 13Z"/></svg>

  <div class="abs col-title" style="left:24px;top:1562px">Corporate<br>Responsibility</div>
  <div class="abs col-title" style="left:156px;top:1562px">Experts With Team<br>Spirit</div>
  <div class="abs col-title" style="left:288px;top:1562px">Diversity, Equity &amp;<br>Inclusion</div>
  <div class="abs col-title" style="left:421px;top:1562px">Diversity, Equity &amp;<br>Inclusion</div>
  <p class="abs col-text" style="left:25px;top:1591px;width:100px">We handle everything from permits to final walkthrough communication every step of the way</p>
  <p class="abs col-text" style="left:157px;top:1591px;width:96px">Experienced professionals committed to precision and safety goal is zero incidents</p>
  <p class="abs col-text" style="left:289px;top:1591px;width:92px">Only top-grade materials used for lasting strength and style our goal is zero incidents</p>
  <p class="abs col-text" style="left:422px;top:1591px;width:92px">Only top-grade materials used for lasting strength and style our goal is zero incidents</p>

  <section class="abs cta">
    <div class="abs" style="left:40px;top:33px;font-size:13px;font-weight:300;line-height:15px">Together, we can make<br>your projects a reality</div>
  </section>
  <div class="photo" style="left:186px;top:1657px;width:128px;height:100px;background:linear-gradient(180deg,#7a1e1e,#e8e4df 35%,#9a8a78)" role="img" aria-label="Bright modern lobby with red ceiling ring"></div>
  <div class="photo" style="left:333px;top:1657px;width:205px;height:100px;background:linear-gradient(135deg,#3a3a3a,#9fb8cc 50%,#2a2a2a)" role="img" aria-label="Escalators in a modern building"></div>

  <div class="abs foot-link" style="left:73px;top:1793px">Services<br>Project<br>About</div>
  <div class="abs foot-link" style="left:186px;top:1793px">About<br>Career<br>Contact</div>
  <div class="abs" style="left:351px;top:1795px;font-size:12px;font-weight:500">+44 120 555 0147</div>
  <div class="abs" style="left:351px;top:1819px;font-size:8px;font-weight:300;line-height:12px">88 Harrow Lane,<br>City of London, United Kingdom</div>
  <div class="abs" style="left:351px;top:1854px;font-size:8px;font-weight:300">hello@kestrada-build.com</div>

  <div class="abs legal" style="left:48px">Privacy Policy</div>
  <div class="abs legal" style="left:90px">.</div>
  <div class="abs legal" style="left:100px">Terms &amp; Conditions</div>
  <div class="abs legal" style="left:351px">Copyright © 2024 Kestrada LLC. All Rights Reserved.</div>

</main>
</body>
</html>
```